GTP biz card

We need a business card design for our new company based in Los Angeles called "Gold Tide Pictures". We develop film and television projects. We work with investors, financiers, film production companies, film distribution and sales companies as well as studios. We would like to incorporate our logo (see attached) on a two-sided card. We need to include: name and title, address, phone, email and company website.

Target Market(s)

Business, financial and studio clients

Industry/Entity Type

Business

Contact Information for Business Card

Two-sided. We are thinking of the logo on one side and the information on the back. Please feel free to be creative! Thanks.

Requirements
Must have
• Please include the following text information, excluding the "CAPS CATEGORY:" and please allow the ability for us to change the name, title and email address for each company employee):
• NAME & TITLE:
• Neil Parker
• Managing Partner
• COMPANY NAME:
• GOLD TIDE PICTURES (please use existing logo)
• COMPANY ADDRESS:
• KTW Studio Park
• 2250 Halverd Street
• Harbor Wing, 4th Floor
• Manhattan Beach, CA 90412
• COMPANY PHONE NUMBER:
• 310-555-0148
• COMPANY WEBSITE ADDRESS:
• www.goldtidepicturesgroup.example
• EMAIL ADDRESS: (only one per card)
• peter@goldtidepicturesgroup.example
• bingo@goldtidepicturesgroup.example
• neil@goldtidepicturesgroup.example

```html
<!DOCTYPE html>
<html lang="en">
<head>
<meta charset="utf-8">
<title>Gold Tide Pictures – Business Card</title>
<link rel="stylesheet" href="https://fonts.googleapis.com/css2?family=Lato:wght@400;700;900&display=swap">
<style>
  :root {
    --bg: #4a3d36;
    --card: #050607;
    --cyan: #3fc3e6;
    --cyan-light: #9be3f4;
    --teal-dark: #163b47;
    --ink: #0a1a20;
    --white: #ffffff;
  }
  * { box-sizing: border-box; margin: 0; padding: 0; }
  html, body { width: 1200px; height: 419px; overflow: hidden; }
  body {
    background: var(--bg);
    font-family: "Lato", Arial, sans-serif;
    position: relative;
  }
  .card {
    position: absolute;
    top: 66px;
    width: 500px;
    height: 286px;
    background: var(--card);
    overflow: hidden;
    box-shadow: 0 10px 24px rgba(0,0,0,.45);
  }
  .card--info { left: 50px; }
  .card--logo { left: 650px; }
  .card__bands { position: absolute; inset: 0; }

  /* info side */
  .brand {
    position: absolute;
    left: 20px;
    top: 72px;
    width: 160px;
    text-align: center;
  }
  .brand__dot {
    display: block;
    width: 56px; height: 56px;
    margin: 0 auto 12px;
    border-radius: 50%;
    background: var(--cyan);
  }
  .brand__name {
    color: var(--cyan);
    font-weight: 900;
    font-size: 12px;
    letter-spacing: 1.5px;
    white-space: nowrap;
  }
  .address {
    position: absolute;
    left: 12px; top: 210px;
    width: 296px;
    border-radius: 0 8px 8px 0;
    background: linear-gradient(90deg, var(--cyan), var(--cyan-light));
    color: var(--ink);
    font-weight: 700;
    font-size: 10px;
    line-height: 15px;
    padding: 4px 0 4px 10px;
    white-space: nowrap;
  }
  .address span { display: block; }
  .person {
    position: absolute;
    left: 300px; top: 30px;
    width: 166px; height: 38px;
    border-radius: 7px;
    background: linear-gradient(90deg, var(--cyan), var(--cyan-light));
    padding: 4px 0 0 24px;
    color: var(--ink);
  }
  .person__name { font-weight: 900; font-size: 15px; line-height: 16px; }
  .person__title { font-size: 10px; font-weight: 700; }
  .contact {
    position: absolute;
    right: 40px;
    color: var(--white);
    font-size: 10.5px;
    font-weight: 700;
    text-align: right;
    white-space: nowrap;
  }
  .contact--phone { top: 94px; }
  .contact--email { top: 128px; font-weight: 400; }
  .contact--web { top: 162px; }
  .contact--web span { color: var(--cyan); }
  .icon-tab {
    position: absolute;
    right: 8px;
    width: 22px; height: 24px;
    border-radius: 5px 0 0 5px;
    background: var(--cyan);
  }
  .icon-tab svg { display: block; margin: 4px auto; }
  .icon-tab--phone { top: 88px; }
  .icon-tab--email { top: 122px; }
  .icon-tab--web { top: 156px; }

  /* logo side */
  .mark {
    position: absolute;
    left: 0; right: 0; top: 64px;
    text-align: center;
  }
  .mark__dot {
    display: block;
    width: 84px; height: 84px;
    margin: 0 auto 18px;
    border-radius: 50%;
    background: var(--cyan);
  }
  .mark__name {
    color: var(--cyan);
    font-weight: 900;
    font-size: 22px;
    letter-spacing: 3px;
  }
</style>
</head>
<body>

<section class="card card--info" aria-label="Business card, information side">
  <svg class="card__bands" viewBox="0 0 500 286" aria-hidden="true">
    <rect x="0" y="0" width="500" height="14" fill="var(--teal-dark)"/>
    <polygon points="0,0 172,0 182,9 0,9" fill="var(--cyan)"/>
    <rect x="0" y="272" width="500" height="14" fill="var(--teal-dark)"/>
    <polygon points="338,263 500,263 500,274 328,274" fill="var(--cyan)"/>
  </svg>

  <div class="brand">
    <span class="brand__dot"></span>
    <div class="brand__name">GOLD TIDE PICTURES</div>
  </div>
  <address class="address" style="font-style:normal">
    <span>KTW Studio Park, 2250 Halverd Street</span>
    <span>Harbor Wing, 4th Floor, Manhattan Beach, CA 90412</span>
  </address>

  <div class="person">
    <div class="person__name">NEIL PARKER</div>
    <div class="person__title">Managing Partner</div>
  </div>

  <p class="contact contact--phone">310-555-0148</p>
  <p class="contact contact--email">neil@goldtidepicturesgroup.example</p>
  <p class="contact contact--web">www.<span>goldtidepicturesgroup.example</span></p>

  <div class="icon-tab icon-tab--phone">
    <svg width="12" height="16" viewBox="0 0 12 16" aria-hidden="true"><rect x="1.5" y="1" width="9" height="14" rx="1.5" fill="none" stroke="var(--ink)" stroke-width="1.5"/><circle cx="6" cy="12.5" r="0.9" fill="var(--ink)"/></svg>
  </div>
  <div class="icon-tab icon-tab--email">
    <svg width="14" height="16" viewBox="0 0 14 16" aria-hidden="true"><rect x="1" y="3.5" width="12" height="9" fill="var(--ink)"/><polyline points="1,3.5 7,9 13,3.5" fill="none" stroke="var(--cyan)" stroke-width="1.2"/></svg>
  </div>
  <div class="icon-tab icon-tab--web">
    <svg width="14" height="16" viewBox="0 0 14 16" aria-hidden="true"><circle cx="7" cy="8" r="5.5" fill="none" stroke="var(--ink)" stroke-width="1.5"/><ellipse cx="7" cy="8" rx="2.2" ry="5.5" fill="none" stroke="var(--ink)" stroke-width="1"/><line x1="1.5" y1="8" x2="12.5" y2="8" stroke="var(--ink)" stroke-width="1"/></svg>
  </div>
</section>

<section class="card card--logo" aria-label="Business card, logo side">
  <svg class="card__bands" viewBox="0 0 500 286" aria-hidden="true">
    <rect x="0" y="0" width="500" height="14" fill="var(--teal-dark)"/>
    <polygon points="0,0 160,0 170,10 0,10" fill="var(--cyan)"/>
    <rect x="0" y="272" width="500" height="14" fill="var(--teal-dark)"/>
    <polygon points="340,262 500,262 500,274 330,274" fill="var(--cyan)"/>
  </svg>
  <div class="mark">
    <span class="mark__dot"></span>
    <div class="mark__name">GOLD TIDE PICTURES</div>
  </div>
</section>

</body>
</html>
```